BOLD & MINIMALIST DESIGN NEEDED

We want a very bold but minimalistic business card design that is impactful and utilizes both sides of the business card. Our current logo is included for your use.

We want bold fonts and good use of negative space. We don't want the logo to overpower the design.

Target Market(s)

Professionals who are building new commercial buildings.

Industry/Entity Type

Construction

Contact Information for Business Card

Name, Title, email, office phone, cell phone, website

Font styles to use
Serif
Sans Serif

Requirements
Must have
• Bold design!

```html
<!DOCTYPE html>
<html lang="en">
<head>
<meta charset="utf-8">
<title>Halvorne Business Card</title>
<link href="https://fonts.googleapis.com/css2?family=Poppins:wght@400;500;600;700&display=swap" rel="stylesheet">
<style>
  :root {
    --backdrop: #262626;
    --card-top: #1c1c1c;
    --card-bottom: #2e2e2e;
    --text-light: #e6e6e6;
    --text-muted: #cfcfcf;
    --accent-green: #7cc242;
  }
  * { margin: 0; padding: 0; box-sizing: border-box; }
  html, body {
    width: 1200px;
    height: 576px;
    overflow: hidden;
    background: var(--backdrop);
    font-family: "Poppins", sans-serif;
  }
  .canvas {
    position: relative;
    width: 1200px;
    height: 576px;
  }
  .card {
    position: absolute;
    top: 139px;
    height: 292px;
    border-radius: 8px;
    background: linear-gradient(160deg, var(--card-top) 0%, var(--card-bottom) 100%);
  }
  .card--front { left: 102px; width: 484px; }
  .card--back  { left: 597px; width: 479px; }

  .brand {
    position: absolute;
    display: flex;
    align-items: center;
    gap: 10px;
    color: var(--text-light);
    font-weight: 700;
    letter-spacing: 0.02em;
    white-space: nowrap;
  }
  .brand__square {
    background: var(--accent-green);
    flex: none;
  }
  .card--front .brand {
    left: 50%;
    top: 50%;
    transform: translate(-50%, -50%);
    font-size: 40px;
  }
  .card--front .brand__square { width: 22px; height: 22px; }

  .card--back .brand {
    left: 138px;
    top: 146px;
    transform: translate(-50%, -50%);
    font-size: 22px;
    gap: 7px;
  }
  .card--back .brand__square { width: 12px; height: 12px; }

  .contact {
    position: absolute;
    left: 265px;
    top: 86px;
  }
  .contact__name {
    color: var(--accent-green);
    font-size: 20px;
    font-weight: 500;
    line-height: 1.2;
  }
  .contact__title {
    color: var(--text-muted);
    font-size: 11px;
    margin-top: 2px;
  }
  .contact__list {
    list-style: none;
    margin-top: 22px;
  }
  .contact__item {
    display: flex;
    align-items: center;
    gap: 8px;
    color: var(--text-light);
    font-size: 12.5px;
    line-height: 17px;
    white-space: nowrap;
  }
  .contact__icon { width: 10px; height: 10px; fill: var(--accent-green); flex: none; }
</style>
</head>
<body>
<div class="canvas">
  <section class="card card--front">
    <div class="brand"><span class="brand__square"></span>HALVORNE</div>
  </section>

  <section class="card card--back">
    <div class="brand"><span class="brand__square"></span>HALVORNE</div>
    <div class="contact">
      <p class="contact__name">Daniel Reyes</p>
      <p class="contact__title">Director</p>
      <ul class="contact__list">
        <li class="contact__item">
          <svg class="contact__icon" viewBox="0 0 10 10"><path d="M1 3c0-1 1-2 4-2s4 1 4 2v1H7V3H3v1H1z M2 5h6l1 4H1z"/></svg>
          555-014-2270
        </li>
        <li class="contact__item">
          <svg class="contact__icon" viewBox="0 0 10 10"><path d="M0 2h10v6H0z M0.5 2.5 5 6l4.5-3.5" stroke="#1f1f1f" stroke-width="0.8"/></svg>
          daniel@halvorne.com
        </li>
        <li class="contact__item">
          <svg class="contact__icon" viewBox="0 0 10 10"><circle cx="5" cy="5" r="4.5"/><path d="M0.5 5h9M5 0.5c-2 2.5-2 6.5 0 9M5 0.5c2 2.5 2 6.5 0 9" stroke="#1f1f1f" stroke-width="0.7" fill="none"/></svg>
          www.halvorne.com
        </li>
      </ul>
    </div>
  </section>
</div>
</body>
</html>
```